Vindgerdi - Start-up company selling electricity

Hello let me tell you about Vindgerdi.

Vindgerdi is start-up company selling electricity in Iceland. The operations of the company consist of making power usage forecasts for our customers, purchasing the electricity wholesale from the energy producers, and selling the electricity to the consumer. We are focused on tech by using optimization and machine learning to minimize electricity prices to our customers. Our marketing strategy is to portray a tech company mindset and to show dedication to driving down the electricity price on the market.

We need your help to make our website pop. Possible concepts to work with are as follows:

- Iceland the land of ice and fire
- Green energy
- Innovation
- Tech and data science

Link to our website: https://prufa.vindgerdi-example.is/
We are open to ideas.
Thank you!

Target Market(s)

Electricity consumers both homes and companies.

Number of Pages Required

1 page

Font styles to use
Serif
Sans Serif

```html
<!DOCTYPE html>
<html lang="is">
<head>
<meta charset="utf-8">
<title>Vindgerdi</title>
<link href="https://fonts.googleapis.com/css2?family=Chakra+Petch:wght@400;500&family=Mulish:wght@400&family=Cinzel:wght@400;700&display=swap" rel="stylesheet">
<style>
:root{
  --green:#829d0e;
  --orange:#f95a04;
  --dark:#333333;
  --ink:#222222;
  --white:#ffffff;
  --card-border:#eeeeee;
  --hero-top:#3f5a68;
  --hero-mid:#5d6b70;
  --hero-low:#6e6f62;
}
*{margin:0;padding:0;box-sizing:border-box}
html,body{width:1200px;height:1129px;overflow:hidden;background:var(--white)}
body{position:relative;font-family:"Mulish",sans-serif;color:var(--ink)}
.hero{position:absolute;left:0;top:0;width:1200px;height:400px}
.hero-photo{position:absolute;inset:0;width:1200px;height:400px}
.brand{position:absolute;left:141px;top:36px;display:flex;align-items:center;gap:10px;color:var(--white);font-family:"Cinzel",serif;font-weight:700;font-size:32px;letter-spacing:.5px}
.brand-dot{width:26px;height:26px;border-radius:50%;background:var(--white)}
.nav{position:absolute;top:58px;font-family:"Chakra Petch",sans-serif;font-size:14.5px;color:var(--white)}
.headline{position:absolute;left:0;width:1200px;top:176px;text-align:center;font-family:"Chakra Petch",sans-serif;font-weight:500;font-size:46px;color:var(--white);text-shadow:2px 3px 4px rgba(0,0,0,.45)}
.card{position:absolute;top:440px;width:295px;height:387px;background:var(--white);border:1px solid var(--card-border);box-shadow:0 0 8px rgba(0,0,0,.05);text-align:center}
.icon-ring{position:absolute;left:87px;top:29px;width:121px;height:121px;border-radius:50%;border:2px solid #e4e4e4;background:radial-gradient(circle at 50% 40%,#fafafa,#e8e8e8);display:flex;align-items:center;justify-content:center}
.card-title{position:absolute;left:0;width:100%;top:166px;font-family:"Chakra Petch",sans-serif;font-weight:400;font-size:16px}
.card-text{position:absolute;top:201px;font-size:12.2px;line-height:19.2px}
.btn{position:absolute;top:323px;width:113px;height:39px;color:var(--white);font-family:"Cinzel",serif;font-size:12.5px;letter-spacing:.5px;display:flex;align-items:center;justify-content:center}
.btn-green{background:var(--green)}
.btn-orange{background:var(--orange)}
.price{position:absolute;top:203px;width:120px;text-align:center}
.price-value{font-size:19px;font-family:"Mulish",sans-serif;margin-bottom:6px}
.price-unit{font-size:12px;line-height:16px}
.divider{position:absolute;left:143px;top:195px;width:1px;height:88px;background:#e2e2e2}
.compare{position:absolute;left:0;width:100%;top:296px;font-size:12px}
.footer{position:absolute;left:0;top:902px;width:1200px;height:190px;background:var(--dark);color:var(--white)}
.foot-icon{position:absolute;width:42px;height:42px;border-radius:50%;background:var(--green);border:2px solid #f0f0f0;display:flex;align-items:center;justify-content:center}
.contact{position:absolute;left:198px;top:35px;font-size:14px;line-height:21px}
.address-title{position:absolute;left:846px;top:35px;font-family:"Cinzel",serif;font-size:15px;letter-spacing:1px}
.address{position:absolute;left:846px;top:60px;font-size:12.5px}
.foot-brand{position:absolute;left:0;width:1200px;top:40px;display:flex;flex-direction:column;align-items:center;gap:8px;font-family:"Cinzel",serif;font-size:16px}
.foot-brand .mark{width:48px;height:48px;border-radius:50%;background:var(--green)}
.company{position:absolute;left:0;width:1200px;top:133px;text-align:center;font-family:"Cinzel",serif;font-size:13px;line-height:20px;letter-spacing:.4px}
.copyright{position:absolute;left:0;top:1092px;width:1200px;height:37px;background:var(--green);color:var(--white);font-size:12.5px;display:flex;align-items:center;justify-content:center}
</style>
</head>
<body>
<header class="hero">
  <svg class="hero-photo" viewBox="0 0 1200 400" role="img" aria-label="Photo of a town by the sea with mountains behind it">
    <defs>
      <linearGradient id="heroFill" x1="0" y1="0" x2="0" y2="1">
        <stop offset="0" stop-color="var(--hero-top)"/>
        <stop offset=".5" stop-color="var(--hero-mid)"/>
        <stop offset="1" stop-color="var(--hero-low)"/>
      </linearGradient>
    </defs>
    <path d="M0 0H1200V395C1150 360 1110 345 1000 346C820 348 600 392 400 385C230 380 90 360 0 332Z" fill="url(#heroFill)"/>
    <path d="M0 332C90 360 230 380 400 385C600 392 820 348 1000 346C1110 345 1150 360 1200 395" fill="none" stroke="var(--green)" stroke-width="4"/>
  </svg>
  <div class="brand"><span class="brand-dot"></span>VINDGERDI</div>
  <nav>
    <span class="nav" style="left:625px">Viðskiptaskilmálar</span>
    <span class="nav" style="left:805px">Spurt &amp; Svarað</span>
    <span class="nav" style="left:952px;top:61px">Um Vindgerdi</span>
  </nav>
  <h1 class="headline">Sama Rafmagn - Bara Ódýrara!</h1>
</header>

<section class="card" style="left:141px">
  <div class="icon-ring">
    <svg width="44" height="66" viewBox="0 0 44 66" fill="none" stroke="var(--green)" stroke-width="2.5" stroke-linecap="round" stroke-linejoin="round">
      <path d="M12 2V14M32 2V14M4 14H40V26C40 36 32 42 22 42C12 42 4 36 4 26Z"/>
      <path d="M24 20L18 28H26L20 36"/>
      <path d="M22 42V52C22 58 28 62 34 62"/>
    </svg>
  </div>
  <h2 class="card-title">Velkomin Í Viðskipti</h2>
  <p class="card-text" style="left:28px;width:238px">Lorem ipsum dolor sit a consectetuer adipiscing elit, sed diam nonummy nibh euismod tincidunt ut laoreet dolore magna aliquam erat volutpat.Ut wisi enim ad minim veniam quis.</p>
  <a class="btn btn-green" style="left:26px">FYRIRTÆKI</a>
  <a class="btn btn-orange" style="left:146px">HEIMILI</a>
</section>

<section class="card" style="left:453px">
  <div class="icon-ring">
    <svg width="50" height="64" viewBox="0 0 50 64" fill="none" stroke="var(--green)" stroke-width="2.5" stroke-linejoin="round">
      <path d="M2 2H40L48 10V62H2Z"/>
      <path d="M12 14H20M30 14H38M12 20H20M30 20H38M25 9V25"/>
      <rect x="10" y="30" width="7" height="6"/><rect x="10" y="40" width="7" height="6"/><rect x="10" y="50" width="7" height="6"/>
      <path d="M22 31H40M22 35H40M22 41H40M22 45H40M22 51H40M22 55H40"/>
    </svg>
  </div>
  <h2 class="card-title">Verðskrá</h2>
  <div class="price" style="left:9px"><div class="price-value">6.95</div><div class="price-unit">krónur / kWst</div></div>
  <div class="divider"></div>
  <div class="price" style="left:147px;width:128px"><div class="price-value">6.22</div><div class="price-unit">krónur / kWst<br>rafmagnskynding</div></div>
  <p class="compare">Gerðu verðsamanburð</p>
  <a class="btn btn-green" style="left:91px">VERÐVAKT</a>
</section>

<section class="card" style="left:764px">
  <div class="icon-ring">
    <svg width="48" height="76" viewBox="0 0 48 76" fill="none" stroke="var(--green)" stroke-width="3" stroke-linejoin="round">
      <path d="M32 2L4 42H22L14 74L44 30H26Z"/>
    </svg>
  </div>
  <h2 class="card-title">Framtíðin Er Spennandi</h2>
  <p class="card-text" style="left:38px;width:219px">Gerum raforkukerfið snallara saman. Vindgerdi notar gervigreind, gagnavísindi og sjálfvirkni til að lágmarka kostnað og stuðla að okrujöfnuði</p>
  <a class="btn btn-green" style="left:103px;top:322px">VITA MEIRA</a>
</section>

<footer class="footer">
  <div class="foot-icon" style="left:141px;top:36px">
    <svg width="22" height="18" viewBox="0 0 22 18" fill="none" stroke="var(--white)" stroke-width="1.5"><rect x="1" y="1" width="20" height="16" rx="1"/><path d="M1 2L11 10L21 2"/></svg>
  </div>
  <div class="contact">vindgerdi@vindgerdi-example.is<br>400-1234</div>
  <div class="foot-brand"><span class="mark"></span>Vindgerdi</div>
  <div class="company">Vindgerdi Ehf<br>Kennitala: 510101-2290 &nbsp; · &nbsp; Vskm Númer: 204718</div>
  <div class="foot-icon" style="left:793px;top:36px">
    <svg width="16" height="22" viewBox="0 0 16 22" fill="none" stroke="var(--white)" stroke-width="1.5"><path d="M8 21C8 21 1 13 1 8A7 7 0 0 1 15 8C15 13 8 21 8 21Z"/><circle cx="8" cy="8" r="2.5"/></svg>
  </div>
  <div class="address-title">HEIMILISFANG</div>
  <div class="address">Vindási 8 170 Seltjarnarnesi</div>
</footer>
<div class="copyright">Copyright © Vindgerdi 2021 Allur Réttur Áskilin</div>
</body>
</html>
```